Business Card Design needed for start up company Halvora

In need of a new business card designed for a start up company based in Sydney, Halvora is a new start up innovative Company, our mission it to make property accessible for everyday Australian and to become the leading Real Estate platform in Australia. We want it to be fresh and clean.

Industry/Entity Type

Financial

Contact Information for Business Card

Section for Name
Section for Title

HALVORA - The Strength of Pooling
Mobile:
Direct:

Font styles to use
Sans Serif

Colors
33a6d7
0692cd
0255a3
ffffff

Requirements
Must have
• Logo, all business card details

```html
<!DOCTYPE html>
<html lang="en">
<head>
<meta charset="utf-8">
<title>Halvora Business Card</title>
<link rel="stylesheet" href="https://fonts.googleapis.com/css2?family=Open+Sans:wght@400;600;800&display=swap">
<style>
  :root {
    --stage: #e9e7e4;
    --card: #141518;
    --card-edge: #0c0d0f;
    --pattern-a: #1c1d21;
    --pattern-b: #232429;
    --sky: #33a6d7;
    --azure: #0692cd;
    --navy: #0255a3;
    --white: #ffffff;
    --silver: #b9b9bb;
    --muted: #8d8e92;
  }
  * { box-sizing: border-box; margin: 0; padding: 0; }
  html, body { width: 1200px; height: 864px; overflow: hidden; }
  body {
    background: var(--stage);
    font-family: "Open Sans", Arial, sans-serif;
    position: relative;
  }
  .card {
    position: absolute;
    background: var(--card);
    border-radius: 4px;
    box-shadow: 0 10px 28px rgba(0,0,0,.28);
    overflow: hidden;
  }
  /* back side */
  .card--back { left: 70px; top: 100px; width: 540px; height: 310px; }
  .back-texture {
    position: absolute; inset: 0;
    background: linear-gradient(135deg, var(--pattern-b), var(--pattern-a) 60%, var(--card-edge));
  }
  .back-brand {
    position: absolute; left: 210px; top: 190px;
    display: flex; align-items: center; gap: 10px;
  }
  .brand-dot { border-radius: 50%; flex: none; }
  .back-brand .brand-dot { width: 40px; height: 40px; background: var(--silver); }
  .back-brand .brand-name {
    font-weight: 800; font-size: 36px; letter-spacing: 1px; color: var(--silver);
    white-space: nowrap;
  }
  .back-tagline {
    position: absolute; left: 212px; top: 246px;
    font-size: 14px; color: var(--muted);
  }
  /* front side */
  .card--front { left: 560px; top: 440px; width: 580px; height: 330px; }
  .front-brand {
    position: absolute; left: 36px; top: 138px;
    display: flex; align-items: center; gap: 10px;
  }
  .front-brand .brand-dot { width: 46px; height: 46px; background: var(--sky); }
  .front-brand .brand-name {
    font-weight: 800; font-size: 36px; letter-spacing: .5px; color: var(--navy);
    white-space: nowrap;
  }
  .divider {
    position: absolute; left: 332px; top: 50px; width: 1px; height: 230px;
    background: linear-gradient(to bottom, transparent, var(--silver) 30%, var(--silver) 70%, transparent);
  }
  .contact { position: absolute; left: 354px; top: 74px; color: var(--white); }
  .contact-name { font-weight: 600; font-size: 17px; color: var(--navy); letter-spacing: .5px; }
  .contact-title { font-size: 15px; color: var(--azure); margin-bottom: 10px; }
  .contact-address { font-size: 14px; line-height: 20px; }
  .contact-list { list-style: none; margin-top: 2px; }
  .contact-list li {
    display: flex; align-items: center; gap: 10px;
    font-size: 14px; line-height: 22px; white-space: nowrap;
  }
  .contact-list svg { width: 11px; height: 11px; fill: var(--silver); flex: none; }
</style>
</head>
<body>
  <section class="card card--back" aria-label="Card back">
    <div class="back-texture" role="img" aria-label="Faint repeating brand texture in dark greys"></div>
    <div class="back-brand">
      <span class="brand-dot"></span>
      <span class="brand-name">HALVORA</span>
    </div>
    <p class="back-tagline">The Strength of Pooling</p>
  </section>

  <section class="card card--front" aria-label="Card front">
    <div class="front-brand">
      <span class="brand-dot"></span>
      <span class="brand-name">HALVORA</span>
    </div>
    <div class="divider"></div>
    <div class="contact">
      <p class="contact-name">ELIAS MARROW</p>
      <p class="contact-title">CEO/FOUNDER</p>
      <p class="contact-address">42 Wattle Grove<br>Sydney, NSW 2000</p>
      <ul class="contact-list">
        <li><svg viewBox="0 0 12 12"><path d="M1 4 Q6 0 11 4 L9 6 L8 4.5 Q6 4 4 4.5 L3 6 Z M3 7 H9 V11 H3 Z"/></svg>02 5550 1946</li>
        <li><svg viewBox="0 0 12 12"><path d="M3 0 H9 V12 H3 Z M4 1.5 V9.5 H8 V1.5 Z"/></svg>0412 555 781</li>
        <li><svg viewBox="0 0 12 12"><path d="M0 2 H12 V10 H0 Z"/></svg>elias@halvora.au</li>
        <li><svg viewBox="0 0 12 12"><circle cx="6" cy="6" r="6"/></svg>www.halvora.au</li>
      </ul>
    </div>
  </section>
</body>
</html>
```